Kestrel Motion LLC Sports Therapy and Soft Tissue Injury solutions

We are a company that specializes in Sports Therapy, Physical therapy, muscular rehab, nutrition plans, and personal training. Kestrel Motion travels around the country and world treating athletes and people in the workforce that have Soft Tissue injuries. We are legally partnered with VMR(Vantor Muscle Recovery/vantorrecovery.example) in treating endurance athletes ex. SteelRidge triathalon. We educate our patients on how to sustain a healthy lifestyle.We need a web design that has a Home page summarizing our services, a Physical therapy page, a Personal training and nutrition page. Our ultimate goal is to build relationships with fitness centers, training facilities, and companies that are implementing preventative health measures for their employees. We want to incorporate the VMR logo and SteelRidge logo attached in the website but, we want to use our own name (Kestrel Motion LLC) as the main draw. We will provide literature for the website.

Target Market(s)

Grindlane training gyms, Fitness centers, Dance studios, Companies looking for Corporate Wellness programs

Industry/Entity Type

Health And Wellness

Number of Pages Required

4 page

Font styles to use
Sans Serif

Requirements
Must have
• Stock Photos of Athletes training. Examples of Endurance Athletes and Cross training. A mesh of as many sports and training methods as possible. We are a new company and don't have many photos. Easy accessibility to change and add text as the company grows. Vantor Muscle recovery logo incorporated in the back ground of the website. Always visible but does not take over the web page
Nice to have
• Sleek and cool, and masculine design. We want the website to stand out without focusing on one individual. We want to use the website to brand the company (Kestrel Motion LLC) with easy access to social media platforms

```html
<!DOCTYPE html>
<html lang="en">
<head>
<meta charset="utf-8">
<title>Kestrel Motion LLC — Sports Therapy</title>
<link rel="stylesheet" href="https://fonts.googleapis.com/css2?family=Mulish:wght@400;600;700;800&family=Open+Sans:wght@400;600&display=swap">
<style>
:root{
  --green:#5aa31c;
  --green-dark:#3d7a12;
  --green-logo:#4fa128;
  --orange:#ff6a13;
  --orange-light:#ff8a2a;
  --ink:#333333;
  --muted:#6b6b6b;
  --footer:#333333;
  --footer-text:#cfcfcf;
  --white:#ffffff;
  --line:#e3e3e3;
}
*{margin:0;padding:0;box-sizing:border-box}
html,body{width:1200px;height:2302px;overflow:hidden}
body{position:relative;background:var(--white);font-family:"Open Sans",Arial,sans-serif;color:var(--ink)}
.abs{position:absolute}
.heading{font-family:"Mulish","Helvetica Neue",sans-serif}

/* header */
.site-header{left:0;top:0;width:1200px;height:95px;background:var(--white)}
.brand{left:127px;top:30px;font-family:"Mulish",sans-serif;font-size:28px;font-weight:600;color:var(--green-logo)}
.main-nav{top:38px;font-family:"Mulish",sans-serif;font-size:16px;color:#555}
.main-nav.active{color:var(--green)}

/* hero */
.hero{left:0;top:95px;width:1200px;height:525px;background:linear-gradient(100deg,#5b5f63 0%,#8a8f93 40%,#6d7378 70%,#3e4247 100%)}
.hero-panel{left:127px;top:264px;width:405px;height:230px;background:rgba(84,170,26,.92);color:var(--white);text-align:center}
.hero-kicker{margin-top:32px;font-family:"Mulish",sans-serif;font-size:29px;font-weight:700;letter-spacing:.5px}
.hero-title{font-family:"Mulish",sans-serif;font-size:41px;font-weight:800;line-height:1.1;letter-spacing:.5px}
.hero-sub{margin-top:10px;font-size:13px;line-height:19px}
.hero-btn{display:inline-block;margin-top:16px;width:129px;height:35px;border:1.5px solid var(--white);font-size:13px;line-height:32px;font-weight:600;letter-spacing:.5px}
.dots{left:563px;top:580px;display:flex;gap:8px}
.dot{width:14px;height:14px;border-radius:50%;background:var(--white)}
.dot.current{background:transparent;border:2px solid var(--white)}

/* mission */
.mission-photo{left:530px;top:620px;width:670px;height:399px;background:radial-gradient(ellipse at 55% 50%,#d8d1c0 0%,#efece6 40%,#ffffff 75%)}
.mission-title{left:133px;top:688px;font-size:31px;font-weight:400;color:#333}
.mission-text{left:133px;top:747px;width:470px;font-size:12.5px;line-height:24px;color:var(--muted)}
.mission-text p+p{margin-top:11px}
.btn-green{left:129px;top:896px;width:121px;height:36px;background:linear-gradient(var(--green),var(--green-dark));color:var(--white);font-size:12px;font-weight:700;text-align:center;line-height:36px;border-radius:2px}

/* services */
.services{left:0;top:1019px;width:1200px;height:450px;background:linear-gradient(180deg,var(--orange-light) 0%,var(--orange) 100%)}
.section-title{width:1200px;text-align:center;font-size:30px;font-weight:400}
.section-title .rule{display:inline-block;vertical-align:middle;width:70px;height:1px;margin:0 14px;position:relative}
.section-title .rule::after{content:"";position:absolute;top:-3px;width:7px;height:7px;border-radius:50%;background:inherit}
.section-title .rule.left::after{right:0}
.section-title .rule.right::after{left:0}
.services .section-title{top:1048px;color:var(--white)}
.services .rule{background:#ffd0b0}
.service{top:1124px;width:300px;text-align:center;color:var(--white)}
.service-icon{display:block;margin:0 auto}
.service-name{margin-top:18px;font-family:"Mulish",sans-serif;font-size:19px;font-weight:600}
.service-desc{margin-top:8px;font-size:11.5px;line-height:19px;color:#ffe3d0}
.service-more{display:block;margin:12px auto 0}
.curve{left:0;top:1420px}

/* blogs */
.blogs-title{top:1456px;color:#333}
.blogs-title .rule{background:#999}
.card{top:1535px;width:310px;height:317px;border:1px solid var(--line);background:var(--white)}
.card-photo{width:100%;height:176px}
.card-body{padding:20px 28px 0}
.card-title{font-family:"Mulish",sans-serif;font-size:19px;font-weight:600;color:#333}
.card-text{margin-top:8px;font-size:12.5px;line-height:20px;color:var(--muted)}
.card-more{margin-top:12px;font-size:13px;color:var(--orange);font-weight:600;display:flex;align-items:center;gap:6px}

/* footer */
.site-footer{left:0;top:1927px;width:1200px;height:375px;background:var(--footer)}
.foot-head{top:1976px;font-family:"Mulish",sans-serif;font-size:21px;color:var(--white)}
.foot-list{top:2020px;list-style:none;font-size:14px;line-height:26.5px;color:var(--footer-text)}
.contact-line{font-size:14px;line-height:26px;color:var(--footer-text);display:flex;gap:10px}
.partner-badge{left:856px}
.foot-rule{left:132px;top:2217px;width:936px;height:1px;background:#4d4d4d}
.copyright{left:138px;top:2244px;font-size:12px;color:var(--footer-text)}
.social{top:2239px;width:30px;height:30px;border:1.5px solid var(--white);border-radius:50%}
</style>
</head>
<body>

<header class="site-header abs">
  <div class="brand abs">Kestrel Motion LLC</div>
  <nav>
    <span class="main-nav abs active" style="left:445px">Home</span>
    <span class="main-nav abs" style="left:514px">Services</span>
    <span class="main-nav abs" style="left:600px">Physical Therapy</span>
    <span class="main-nav abs" style="left:749px">Personal Training</span>
    <span class="main-nav abs" style="left:899px">Nutrition</span>
    <span class="main-nav abs" style="left:991px">Contact us</span>
  </nav>
</header>

<section class="hero abs" role="img" aria-label="Photo of a coach encouraging an athlete doing push-ups on kettlebells in a gym"></section>
<div class="hero-panel abs">
  <div class="hero-kicker">TRAINING &amp; DIET</div>
  <div class="hero-title">SPORTS THERAPY</div>
  <div class="hero-sub">Cras a ante vitae enim iaculis aliquam<br>Mauris nunc quam venenatis</div>
  <div class="hero-btn">START NOW</div>
</div>
<div class="dots abs"><span class="dot current"></span><span class="dot"></span><span class="dot"></span><span class="dot"></span></div>

<section>
  <div class="mission-photo abs" role="img" aria-label="Photo of a sprinter in a starting crouch"></div>
  <h2 class="mission-title abs heading">Kestrel Motion Mission</h2>
  <div class="mission-text abs">
    <p>statement-We are a company that specializes in Sports Therapy, Physical therapy, muscular rehab, nutrition plans, and personal training. Kestrel Motion travels around the country and world treating athletes and people in the workforce that have Soft tissue injuries.</p>
    <p>We educate our patients on how to sustain a healthy lifestyle!</p>
  </div>
  <div class="btn-green abs">READ MORE</div>
</section>

<section class="services abs" role="img" aria-label="Orange-tinted photo of an athlete training with a jump rope"></section>
<h2 class="section-title abs heading services"><span class="rule left"></span>Our Services<span class="rule right"></span></h2>

<div class="service abs" style="left:142px">
  <svg class="service-icon" width="124" height="124" viewBox="0 0 124 124" fill="none" stroke="#fff" stroke-width="2.5">
    <circle cx="62" cy="62" r="60"/>
    <path d="M38 50h48M40 42v16M46 40v20M84 42v16M78 40v20M50 58v26M74 58v26M46 84h32M56 66h12"/>
  </svg>
  <div class="service-name">Personal Training</div>
  <div class="service-desc">Praesent elementum elit at tellus nec ultricies<br>sit amet porttitor mattis enim in massa libero<br>interdum nec interdum vel</div>
  <svg class="service-more" width="30" height="30" viewBox="0 0 30 30" fill="none" stroke="#fff" stroke-width="1.5"><circle cx="15" cy="15" r="14"/><path d="M13 10l5 5-5 5"/></svg>
</div>

<div class="service abs" style="left:445px">
  <svg class="service-icon" width="124" height="124" viewBox="0 0 124 124" fill="none" stroke="#fff" stroke-width="2.5">
    <circle cx="62" cy="62" r="60"/>
    <circle cx="66" cy="36" r="6" fill="#fff"/>
    <path d="M62 46l-8 18h18M40 64h46M44 64v22M82 64v22M56 64v14M70 64v14"/>
  </svg>
  <div class="service-name">Physical Therapy</div>
  <div class="service-desc">Praesent elementum elit at tellus nec ultricies<br>sit amet porttitor mattis enim in massa libero<br>interdum nec interdum vel</div>
  <svg class="service-more" width="30" height="30" viewBox="0 0 30 30" fill="none" stroke="#fff" stroke-width="1.5"><circle cx="15" cy="15" r="14"/><path d="M13 10l5 5-5 5"/></svg>
</div>

<div class="service abs" style="left:749px">
  <svg class="service-icon" width="124" height="124" viewBox="0 0 124 124" fill="none" stroke="#fff" stroke-width="2.5">
    <circle cx="62" cy="62" r="60"/>
    <path d="M70 46L48 86l30-30z" fill="#fff"/>
    <path d="M70 46l6-10M72 48l10-6M74 50l12-2"/>
  </svg>
  <div class="service-name">Nutrition &amp; Diet</div>
  <div class="service-desc">Praesent elementum elit at tellus nec ultricies<br>sit amet porttitor mattis enim in massa libero<br>interdum nec interdum vel</div>
  <svg class="service-more" width="30" height="30" viewBox="0 0 30 30" fill="none" stroke="#fff" stroke-width="1.5"><circle cx="15" cy="15" r="14"/><path d="M13 10l5 5-5 5"/></svg>
</div>

<svg class="curve abs" width="1200" height="52" viewBox="0 0 1200 52">
  <path d="M0 52 Q600 -14 1200 52 Z" fill="#ffffff"/>
  <path d="M262 19 Q600 0 968 19" fill="none" stroke="var(--green)" stroke-width="5"/>
</svg>

<h2 class="section-title abs heading blogs-title"><span class="rule left"></span>Our Blogs<span class="rule right"></span></h2>

<article class="card abs" style="left:127px">
  <div class="card-photo" role="img" aria-label="Photo of athletes training with battle ropes in a gym" style="background:linear-gradient(135deg,#3b3f44,#8d8f92 60%,#5c6168)"></div>
  <div class="card-body">
    <h3 class="card-title">Blog Tittle here</h3>
    <p class="card-text">Proin nulla arcu nonummy luctus dictum<br>eget fermentum et lorem</p>
    <div class="card-more">READ MORE <svg width="16" height="14" viewBox="0 0 16 14"><path d="M0 7h11M8 2l6 5-6 5" fill="none" stroke="var(--orange)" stroke-width="2.5"/></svg></div>
  </div>
</article>

<article class="card abs" style="left:445px">
  <div class="card-photo" role="img" aria-label="Photo of a fresh green salad in a white bowl" style="background:linear-gradient(135deg,#8c6a4a,#8fb45a 45%,#c9d8b0 70%,#7b5b3f)"></div>
  <div class="card-body">
    <h3 class="card-title">Blog Tittle here</h3>
    <p class="card-text">Proin nulla arcu nonummy luctus dictum<br>eget fermentum et lorem</p>
    <div class="card-more">READ MORE <svg width="16" height="14" viewBox="0 0 16 14"><path d="M0 7h11M8 2l6 5-6 5" fill="none" stroke="var(--orange)" stroke-width="2.5"/></svg></div>
  </div>
</article>

<article class="card abs" style="left:765px">
  <div class="card-photo" role="img" aria-label="Photo of a therapist stretching a patient's leg" style="background:linear-gradient(135deg,#e7e7e7,#c8c4c0 55%,#6d6460)"></div>
  <div class="card-body">
    <h3 class="card-title">Blog Tittle here</h3>
    <p class="card-text">Proin nulla arcu nonummy luctus dictum<br>eget fermentum et lorem</p>
    <div class="card-more">READ MORE <svg width="16" height="14" viewBox="0 0 16 14"><path d="M0 7h11M8 2l6 5-6 5" fill="none" stroke="var(--orange)" stroke-width="2.5"/></svg></div>
  </div>
</article>

<footer class="site-footer abs"></footer>
<h4 class="foot-head abs" style="left:143px">Quick Links</h4>
<ul class="foot-list abs" style="left:143px"><li>Home</li><li>About</li><li>How it Works</li><li>Gallery</li></ul>
<h4 class="foot-head abs" style="left:351px">Resources</h4>
<ul class="foot-list abs" style="left:351px"><li>Term of Use</li><li>Testimonials</li><li>Order Now</li><li>Contact Us</li></ul>
<h4 class="foot-head abs" style="left:552px">Contact Us</h4>
<div class="abs" style="left:552px;top:2016px">
  <div class="contact-line">
    <svg width="14" height="20" viewBox="0 0 14 20" style="margin-top:4px"><path d="M7 0a7 7 0 0 1 7 7c0 5-7 13-7 13S0 12 0 7a7 7 0 0 1 7-7z" fill="#fff"/><circle cx="7" cy="7" r="2.5" fill="var(--footer)"/></svg>
    <span>418 Harrow Ridge Road Suite B12<br>Fallbrook, PA 19380</span>
  </div>
  <div class="contact-line" style="margin-top:22px">
    <svg width="14" height="16" viewBox="0 0 14 16" style="margin-top:5px"><path d="M3 0l3 4-2 2c1 2 3 4 5 5l2-2 3 3-2 3C6 15-1 7 1 2z" fill="#fff"/></svg>
    <span>(555) 014-2270</span>
  </div>
  <div class="contact-line">
    <svg width="16" height="12" viewBox="0 0 16 12" style="margin-top:8px"><rect width="16" height="12" fill="#fff"/><path d="M0 0l8 6 8-6" fill="none" stroke="var(--footer)" stroke-width="1.5"/></svg>
    <span>hello@kestrelmotion.example</span>
  </div>
</div>
<div class="partner-badge abs" style="top:2000px;width:190px;height:40px;border-radius:20px;background:#d0202a" role="img" aria-label="Partner badge: VMR, Vantor Muscle Recovery"></div>
<div class="partner-badge abs" style="top:2072px;width:190px;height:38px;background:#ffffff" role="img" aria-label="Partner badge: SteelRidge"></div>

<div class="foot-rule abs"></div>
<div class="copyright abs">© 2017 Company Name&nbsp; All right reserved&nbsp; Term of Use</div>
<span class="social abs" style="left:921px" aria-label="Social profile"></span>
<span class="social abs" style="left:957px" aria-label="Social profile"></span>
<span class="social abs" style="left:993px" aria-label="Social profile"></span>
<span class="social abs" style="left:1029px" aria-label="Social profile"></span>

</body>
</html>
```